Internal Office Slogans / Motto / Vision Statements

Hi. We would like to put up some posters around the office with quotations such as -
-”Do what you do so well that they will want to see it again and bring their friends.”- Hollis Brandt
-Make your customers feel heard and understood. Make your customers feel respected and liked. Make your customers feel appreciated and helped. Understand that you can do none of these things unless you are sincere about them.
Terrence Oakley
- It’s a very predictable and satisfying phenomenon: whenever we get better, our customers do too.
Cal Pruett
-Catch people in the act of performing extraordinary customer service. Treat them like heroes. Tell their stories, far and wide.
Ned Farraday

The purpose of the posters is to reiterate our culture and vision within the organisation. They should be clean, crisp and eye catching, not gaudy or bright. Professional, bold and strong.

The company website and logo is at http://www.nexoraweb.com.au
Print size will be A1

Thanks for participating & looking forward to seeing your great work.
Updates

Hi All. . 

So to reiterate we are looking for one background design to be used for multiple quotes...  The list of quotes are as follows: 

Support and or Sales Office

 

Make your customers feel heard and understood.Make your customers feel respected and liked. Make your customers feelappreciated and helped. Understand that you can do none of these things unlessyou are sincere about them.

Terrence Oakley

 

Nothing liberates our greatness like the desireto help, the desire to serve

Dorothea Quill

 

It’s a very predictable and satisfying phenomenon:whenever we get better, our customers do too.

Cal Pruett

 

Success means we go to sleep at night knowingthat our talents and abilities were used in a way that served others.

Dorothea Quill.

 

The sole purpose of business is to create, serveand satisfy a customer, from beginning to end – and that’s everyone’s job.

Ned Farraday

 

We don’t celebrate closing a sale, we celebrateopening a relationship.

Rosalind Hext

I will never make you a promise – unless I giveyou a plan and procedure to make that promise possible.

Bo Tennant

 

Customers feel we take them for granted; onlyshow interest when we want an order; lavish our time on prospects; communicatemainly by invoice; are fixated on big accounts; drop them like hot potatoesonce we have the order; don’t follow through on promises; and satisfy our ownbureaucracy rather than their needs. We can do better than that, much better.

Alan P Merrow.

 

 

General and public area

 

Catch people in the act of performingextraordinary customer service. Treat them like heroes. Tell their stories, farand wide.

Ned Farraday

 

 

We see our customers as invited guests to aparty, and we are the hosts. It’s our job every day to make every importantaspect of the customer experience a little bit better." Carl Voight - Founder andCEO of Halverin

 

"If you do build a great experience,customers tell each other about that. Word of mouth is verypowerful."  Carl Voight

 

It's not a faithin technology. It's faith in people. Rick Palmer

 

“Being the richest man in the cemetery doesn’tmatter to me … Going to bed at night saying we’ve done something wonderful…that’s what matters to me.” Rick Palmer

 

The customer experience is the next competitivebattleground. Lance Morrow, CIO, Vantor Computers

 

”Do what you do so well that they will want tosee it again and bring their friends.”- Hollis Brandt

In the world of internet customer service, it isimportant to remember your competitor is only a mouse click away. FrankHolden (not sure who he is but like the quote).

The customer is why you go to work. If they goaway, you do, too. Peter Lindqvist (?)

 

MaybeSome for Sales or Build Team:

Quality is remembered long after the price is forgotten. Marzetti Family Slogan

```html
<!DOCTYPE html>
<html lang="en">
<head>
<meta charset="utf-8">
<title>Catch People in the Act – Quote Poster</title>
<link rel="stylesheet" href="https://fonts.googleapis.com/css2?family=Questrial&family=Poppins:wght@500;600;700&family=Baumans&display=swap">
<style>
  :root {
    --bg-top: #ece6d9;
    --bg-bottom: #d7cab3;
    --ink: #33302d;
    --catch-blue: #5560b0;
    --act-red: #a55b55;
    --extra-teal: #5f9a86;
    --service-purple: #aa84a4;
    --heroes-orange: #e0a374;
    --wide-green: #5e9249;
    --author-red: #9b302b;
    --rule: #4a4540;
  }
  * { margin: 0; padding: 0; box-sizing: border-box; }
  html, body { width: 848px; height: 1200px; overflow: hidden; }
  body {
    background: linear-gradient(to bottom, var(--bg-top), var(--bg-bottom));
    color: var(--ink);
  }
  .poster { position: relative; width: 848px; height: 1200px; }
  .quote { text-align: center; }
  .line {
    position: absolute;
    left: 0;
    width: 100%;
    line-height: 1;
    white-space: nowrap;
    text-transform: uppercase;
    font-family: "Questrial", "Century Gothic", sans-serif;
  }
  .bold { font-family: "Poppins", "Century Gothic", sans-serif; font-weight: 700; }
  .line-catch      { top: 62px;  font-size: 56px; }
  .line-act        { top: 164px; font-size: 56px; }
  .line-performing { top: 262px; font-size: 54px; font-family: "Poppins", sans-serif; font-weight: 500; letter-spacing: 2px; }
  .line-extra      { top: 358px; font-size: 58px; color: var(--extra-teal); letter-spacing: 2px; }
  .line-customer   { top: 455px; font-size: 58px; letter-spacing: 2px; }
  .line-service    { top: 534px; font-size: 98px; color: var(--service-purple); letter-spacing: 4px; }
  .line-treat      { top: 675px; font-size: 56px; }
  .line-heroes     { top: 744px; font-size: 92px; color: var(--heroes-orange); letter-spacing: 4px; }
  .line-stories    { top: 872px; font-size: 54px; }
  .line-stories .bold { font-weight: 600; }
  .line-wide       { top: 952px; font-size: 40px; color: var(--wide-green); letter-spacing: 1px; }
  .word-catch { color: var(--catch-blue); }
  .word-act   { color: var(--act-red); }
  .divider {
    position: absolute;
    top: 1033px;
    left: 0;
    width: 848px;
    border-top: 4px dashed var(--rule);
  }
  .author {
    position: absolute;
    top: 1094px;
    left: 0;
    width: 100%;
    text-align: center;
    font-family: "Baumans", "Questrial", sans-serif;
    font-size: 58px;
    line-height: 1;
    color: var(--author-red);
    text-transform: uppercase;
    letter-spacing: 1px;
  }
</style>
</head>
<body>
  <main class="poster">
    <blockquote class="quote">
      <p class="line line-catch"><span class="word-catch">Catch</span> people</p>
      <p class="line line-act">In the <span class="bold word-act">act</span> of</p>
      <p class="line line-performing">Performing</p>
      <p class="line line-extra bold">Extraordinary</p>
      <p class="line line-customer bold">Customer</p>
      <p class="line line-service bold">Service.</p>
      <p class="line line-treat">Treat them like</p>
      <p class="line line-heroes bold">Heroes.</p>
      <p class="line line-stories">Tell their <span class="bold">stories.</span></p>
      <p class="line line-wide bold">Far and wide.</p>
    </blockquote>
    <div class="divider"></div>
    <p class="author">-Ned Farraday</p>
  </main>
</body>
</html>
```